Halvor Grading and Septic needs a flyer to submit to contractors to offer our services

I need a sleek profession one page full color high gloss document showcasing our services to give to Mobile Home Companies and contractors that need our services.

Target Market(s)

Home Builders. Mobile Home Salesmen. People Building new homes.

Industry/Entity Type

Construction

Font styles to use
Serif
Sans Serif

Requirements
Must have
• Phone Number. Email address. Logo. Services offered: Mobile Home Pads, Meter Pole Placement and Connection, Waterline Connection, On Site Septic System Installs
Should not have
• Jokes, Nothing trying to be cute

```html
<!DOCTYPE html>
<html lang="en">
<head>
<meta charset="utf-8">
<title>Halvor Grading and Septic – Services Flyer</title>
<link rel="stylesheet" href="https://fonts.googleapis.com/css2?family=Oswald:wght@500;600;700&family=EB+Garamond:wght@600;700&display=swap">
<style>
  :root {
    --backdrop: #252525;
    --navy: #0f4c81;
    --sky: #2a86bf;
    --white: #ffffff;
    --red-dark: #6e0d12;
    --red-bright: #e51e26;
    --sand: #c79a63;
  }
  * { margin: 0; padding: 0; box-sizing: border-box; }
  html, body { width: 1200px; height: 1200px; overflow: hidden; background: var(--backdrop); }
  .flyer {
    position: absolute; left: 232px; top: 84px; width: 737px; height: 1033px;
    background: var(--white); overflow: hidden;
  }
  .abs { position: absolute; }

  .brand { left: 26px; top: 44px; width: 290px; }
  .brand-name {
    display: flex; align-items: center; gap: 10px;
    font-family: "Oswald", sans-serif; font-weight: 700; color: var(--navy);
    font-size: 34px; line-height: 1.05; text-transform: uppercase;
  }
  .brand-mark { width: 20px; height: 20px; background: var(--navy); flex: none; }
  .brand-sub {
    font-family: "Oswald", sans-serif; font-weight: 700; color: var(--navy);
    font-size: 34px; line-height: 1.05; text-transform: uppercase; margin-top: 2px;
  }
  .brand-phone {
    font-family: "Oswald", sans-serif; font-weight: 700; color: var(--navy);
    font-size: 20px; letter-spacing: 2px; margin-top: 8px;
  }

  .headline-panel {
    left: 0; top: 186px; width: 360px; height: 211px; background: var(--navy);
    clip-path: polygon(0 0, 352px 0, 292px 211px, 0 211px);
  }
  .headline {
    left: 24px; top: 194px;
    font-family: "Oswald", sans-serif; font-weight: 600; color: var(--white);
    font-size: 54px; line-height: 62px; letter-spacing: 0.2px;
  }

  .photo { background: var(--sand); }
  .photo-dig {
    left: 0; top: 0; width: 737px; height: 397px;
    clip-path: polygon(404px 0, 737px 0, 737px 397px, 292px 397px);
    background:
      linear-gradient(180deg, #5f8a4a 0%, #7da25e 28%, #b9956a 45%, #c9a06a 70%, #b68553 100%);
  }
  .slant-stripe {
    left: 0; top: 0; width: 737px; height: 397px; background: var(--sky);
    clip-path: polygon(396px 0, 404px 0, 292px 397px, 284px 397px);
  }

  .tagline-band {
    left: 0; top: 397px; width: 737px; height: 48px; background: var(--sky);
    display: flex; align-items: center; justify-content: center;
    font-family: "EB Garamond", serif; font-weight: 700; color: var(--white);
    font-size: 25.5px; letter-spacing: 0.2px;
  }

  .photo-tank {
    left: 0; top: 445px; width: 400px; height: 262px;
    clip-path: polygon(0 0, 395px 0, 321px 262px, 0 262px);
    background: linear-gradient(180deg, #5a97d6 0%, #7fa97a 30%, #c8a57a 55%, #d4b58c 100%);
  }
  .photo-lift {
    left: 330px; top: 445px; width: 407px; height: 262px;
    clip-path: polygon(77px 0, 407px 0, 407px 262px, 2px 262px);
    background: linear-gradient(180deg, #2f6fc4 0%, #5a93d8 45%, #7aa35c 72%, #4f8a3a 100%);
  }

  .services-title {
    left: 150px; top: 716px; width: 437px; height: 70px;
  }
  .services-title span {
    position: absolute; left: 0; right: 0; top: 8px; text-align: center;
    font-family: "Oswald", sans-serif; font-weight: 600; color: var(--navy);
    font-size: 38px; line-height: 50px;
  }

  .services-panel {
    left: 0; top: 793px; width: 737px; height: 240px;
    background: linear-gradient(90deg, var(--red-dark) 0%, #a4151b 50%, var(--red-bright) 100%);
  }
  .service { display: flex; align-items: center; gap: 14px; }
  .service-icon { width: 72px; height: 60px; flex: none; }
  .service-label {
    font-family: "EB Garamond", serif; font-weight: 700; color: var(--white);
    font-size: 21.5px; line-height: 26px; white-space: nowrap;
  }
  .svc-1 { left: 22px; top: 802px; }
  .svc-2 { left: 338px; top: 802px; }
  .svc-3 { left: 22px; top: 878px; }
  .svc-4 { left: 338px; top: 878px; align-items: flex-start; }
  .svc-4 .service-label { padding-top: 5px; }

  .contact-tab {
    left: 541px; top: 917px; width: 196px; height: 46px; background: var(--white);
    clip-path: polygon(14px 0, 196px 0, 196px 46px, 0 46px);
    border-top: 4px solid var(--navy);
  }
  .contact-tab-edge {
    left: 535px; top: 917px; width: 202px; height: 46px; background: var(--navy);
    clip-path: polygon(14px 0, 202px 0, 202px 4px, 18px 4px, 6px 46px, 0 46px);
  }
  .contact-label {
    left: 556px; top: 918px; width: 170px; text-align: right;
    font-family: "Oswald", sans-serif; font-weight: 600; color: var(--navy);
    font-size: 29px; line-height: 42px;
  }

  .contact-bar {
    left: 0; top: 963px; width: 737px; height: 70px; background: var(--navy);
    clip-path: polygon(50px 0, 737px 0, 737px 70px, 26px 70px);
  }
  .contact-phone {
    left: 62px; top: 968px; display: flex; align-items: center; gap: 8px;
    font-family: "Oswald", sans-serif; font-weight: 500; color: var(--white);
    font-size: 34px; line-height: 52px;
  }
  .contact-email {
    left: 364px; top: 974px; display: flex; align-items: center; gap: 8px;
    font-family: "EB Garamond", serif; font-weight: 600; color: var(--white);
    font-size: 18.5px; line-height: 40px;
  }
</style>
</head>
<body>
<main class="flyer">
  <div class="abs photo photo-dig" role="img" aria-label="Excavator digging a septic trench beside a mobile home while a worker checks the trench floor"></div>
  <div class="abs slant-stripe"></div>

  <div class="abs brand">
    <div class="brand-name"><span class="brand-mark"></span>Halvor Grading</div>
    <div class="brand-sub">and Septic</div>
    <div class="brand-phone">903.555.0147</div>
  </div>

  <div class="abs headline-panel"></div>
  <h1 class="abs headline">Professional<br>Wastewater<br>Management</h1>

  <div class="abs tagline-band">Residential and Commercial Septic Services in East Texas</div>

  <div class="abs photo photo-tank" role="img" aria-label="Excavator beside a newly set concrete septic tank with green access lids"></div>
  <div class="abs photo photo-lift" role="img" aria-label="Crane boom lowering a concrete septic tank into a grassy field as a worker guides it"></div>

  <div class="abs services-title">
    <svg width="437" height="70" viewBox="0 0 437 70" aria-hidden="true">
      <polygon points="0,68 66,58 76,2 362,2 350,58 437,68" fill="var(--navy)"/>
      <polygon points="84,8 354,8 344,56 76,56" fill="var(--white)"/>
    </svg>
    <span>Services Offered:</span>
  </div>

  <div class="abs services-panel"></div>

  <div class="abs service svc-1">
    <svg class="service-icon" viewBox="0 0 72 60" aria-hidden="true">
      <polygon points="10,0 72,0 62,60 0,60" fill="var(--sky)"/>
      <polygon points="14,5 66,5 57,55 5,55" fill="var(--navy)"/>
      <g fill="none" stroke="var(--white)" stroke-width="2">
        <path d="M20 24 L36 12 L52 24"/>
        <rect x="20" y="24" width="32" height="18"/>
        <rect x="24" y="28" width="7" height="6"/>
        <rect x="41" y="28" width="7" height="6"/>
        <rect x="33" y="28" width="6" height="14"/>
        <circle cx="26" cy="46" r="2.5"/><circle cx="46" cy="46" r="2.5"/>
      </g>
    </svg>
    <span class="service-label">Mobile Home Pads</span>
  </div>

  <div class="abs service svc-2">
    <svg class="service-icon" viewBox="0 0 72 60" aria-hidden="true">
      <polygon points="10,0 72,0 62,60 0,60" fill="var(--sky)"/>
      <polygon points="14,5 66,5 57,55 5,55" fill="var(--navy)"/>
      <g fill="none" stroke="var(--white)" stroke-width="2">
        <path d="M30 14 h12 M36 14 v6"/>
        <rect x="18" y="22" width="10" height="8"/>
        <path d="M28 20 h16 v18 h-8 v-8 h-8"/>
        <path d="M40 42 q-2 4 0 5 q2 -1 0 -5"/>
      </g>
    </svg>
    <span class="service-label">Waterline Connection</span>
  </div>

  <div class="abs service svc-3">
    <svg class="service-icon" viewBox="0 0 72 60" aria-hidden="true">
      <polygon points="10,0 72,0 62,60 0,60" fill="var(--sky)"/>
      <polygon points="14,5 66,5 57,55 5,55" fill="var(--navy)"/>
      <g fill="none" stroke="var(--white)" stroke-width="2">
        <path d="M20 16 h32 M24 16 v-3 M30 16 v-3 M42 16 v-3 M48 16 v-3"/>
        <path d="M36 16 v28 M28 16 l8 10 l8 -10"/>
        <path d="M26 46 h20"/>
      </g>
    </svg>
    <span class="service-label">Meter Pole Placement<br>and Connection</span>
  </div>

  <div class="abs service svc-4">
    <svg class="service-icon" viewBox="0 0 72 60" aria-hidden="true">
      <polygon points="10,0 72,0 62,60 0,60" fill="var(--sky)"/>
      <polygon points="14,5 66,5 57,55 5,55" fill="var(--navy)"/>
      <g fill="none" stroke="var(--white)" stroke-width="2">
        <rect x="32" y="10" width="8" height="5"/>
        <rect x="26" y="15" width="20" height="32" rx="4"/>
        <path d="M20 24 h6 M46 24 h6"/>
        <path d="M30 36 h12 M30 40 h12 M30 44 h12"/>
      </g>
    </svg>
    <span class="service-label">On Site Septic System Installs</span>
  </div>

  <div class="abs contact-tab-edge"></div>
  <div class="abs contact-tab"></div>
  <div class="abs contact-label">Contact Us:</div>

  <div class="abs contact-bar"></div>
  <div class="abs contact-phone">
    <svg width="26" height="26" viewBox="0 0 24 24" aria-hidden="true">
      <path d="M6.6 10.8a15 15 0 0 0 6.6 6.6l2.2-2.2a1 1 0 0 1 1-.25 11.4 11.4 0 0 0 3.6.57 1 1 0 0 1 1 1V20a1 1 0 0 1-1 1A17 17 0 0 1 3 4a1 1 0 0 1 1-1h3.5a1 1 0 0 1 1 1c0 1.250.2 2.450.57 3.57a1 1 0 0 1-.25 1z" fill="none" stroke="var(--white)" stroke-width="1.8"/>
    </svg>
    (903) 555-0147
  </div>
  <div class="abs contact-email">
    <svg width="16" height="13" viewBox="0 0 16 13" aria-hidden="true">
      <rect x="1" y="1" width="14" height="11" fill="none" stroke="var(--white)" stroke-width="1.3"/>
      <path d="M1 1 L8 7 L15 1" fill="none" stroke="var(--white)" stroke-width="1.3"/>
    </svg>
    dana@halvorgradingseptic.com
  </div>
</main>
</body>
</html>
```